Business card for medical clinic

I need an upmarket, modern medical/health business card for my clinic

Contact Information for Business Card

name, address, email, qr code

```html
<!DOCTYPE html>
<html lang="en">
<head>
<meta charset="utf-8">
<title>Meridian Care Partners – Business Card</title>
<link rel="stylesheet" href="https://fonts.googleapis.com/css2?family=Montserrat:wght@400;600;700&display=swap">
<style>
  :root {
    --stage: #1c1c1c;
    --navy: #1e2744;
    --sky: #27a9e1;
    --brand-blue: #1b6d9e;
    --ink: #1a1f33;
    --paper: #ffffff;
  }
  * { box-sizing: border-box; margin: 0; padding: 0; }
  html, body {
    width: 1200px; height: 1059px; overflow: hidden;
    background: var(--stage);
    font-family: "Montserrat", sans-serif;
  }
  .card {
    position: absolute;
    overflow: hidden;
  }
  .card--front {
    left: 256px; top: 89px; width: 688px; height: 392px;
    background: var(--paper);
  }
  .card--back {
    left: 253px; top: 546px; width: 694px; height: 395px;
    background: var(--navy);
  }
  .brand {
    position: absolute;
    display: flex; align-items: center; gap: 14px;
    font-weight: 600; letter-spacing: 0.06em; text-transform: uppercase;
    line-height: 1.1;
  }
  .brand__dot {
    width: 26px; height: 26px; border-radius: 50%;
    border: 3px solid currentColor; flex: none;
  }
  .card--front .brand {
    left: 30px; top: 58px; color: var(--brand-blue); font-size: 27px;
  }
  .card--back .brand {
    left: 0; right: 0; top: 172px; justify-content: center;
    color: var(--paper); font-size: 36px;
  }
  .card--back .brand__dot { width: 34px; height: 34px; }
  .accent-bar {
    position: absolute; left: 0; top: 228px; width: 14px; height: 41px;
    background: var(--sky);
  }
  .person__name {
    position: absolute; left: 35px; top: 217px;
    font-size: 24px; font-weight: 700; color: var(--ink);
  }
  .person__role {
    position: absolute; left: 35px; top: 248px;
    font-size: 14px; font-weight: 400; color: var(--ink);
  }
  .divider {
    position: absolute; left: 35px; top: 270px; width: 612px; height: 1.5px;
    background: var(--sky);
  }
  .contact-list {
    position: absolute; left: 35px; top: 288px; list-style: none;
  }
  .contact-list li {
    display: flex; align-items: center; gap: 10px;
    height: 27.5px; font-size: 14.5px; color: var(--ink);
  }
  .contact-list svg { width: 15px; height: 15px; fill: var(--navy); flex: none; }
  .address {
    position: absolute; right: 41px; top: 324px; text-align: right;
    font-size: 14.5px; line-height: 1.25; color: var(--ink);
  }
  .footer-band {
    position: absolute; left: 0; bottom: 0; width: 688px; height: 21px;
  }
</style>
</head>
<body>

<section class="card card--front">
  <div class="brand"><span class="brand__dot"></span><span>Meridian Care Partners</span></div>

  <div class="accent-bar"></div>
  <h1 class="person__name">Daniel Hart</h1>
  <p class="person__role">Managing Director</p>
  <div class="divider"></div>

  <ul class="contact-list">
    <li>
      <svg viewBox="0 0 24 24"><path d="M6.6 10.8a15.1 15.1 0 0 0 6.6 6.6l2.2-2.2c.3-.3.7-.4 1-.2 1.1.4 2.3.6 3.6.6.6 0 1 .4 1 1V20c0 .6-.4 1-1 1A17 17 0 0 1 3 4c0-.6.4-1 1-1h3.5c.6 0 1 .4 1 1 0 1.3.2 2.5.6 3.6.1.3 0 .7-.2 1z"/></svg>
      <span>555.204.7731</span>
    </li>
    <li>
      <svg viewBox="0 0 24 24"><path d="M2 5h20v2l-10 6L2 7z"/><path d="M2 9l10 6 10-6v10H2z"/></svg>
      <span>info@meridiancare.com</span>
    </li>
    <li>
      <svg viewBox="0 0 24 24"><path d="M12 2a10 10 0 1 0 0 20 10 10 0 0 0 0-20zm-1 17.9A8 8 0 0 1 4.1 10L9 15v1a2 2 0 0 0 2 2zm6.9-2.5A2 2 0 0 0 16 16h-1v-3a1 1 0 0 0-1-1H8v-2h2a1 1 0 0 0 1-1V7h2a2 2 0 0 0 2-2v-.4a8 8 0 0 1 2.9 12.8z"/></svg>
      <span>www.meridiancare.com</span>
    </li>
  </ul>

  <address class="address" style="font-style:normal">
    240 Cedar Hollow Road<br>Brandon, MS 39047
  </address>

  <svg class="footer-band" viewBox="0 0 688 21" aria-hidden="true">
    <polygon points="0,0 356,0 326,21 0,21" fill="var(--navy)"/>
    <polygon points="368,0 688,0 688,21 338,21" fill="var(--sky)"/>
  </svg>
</section>

<section class="card card--back">
  <div class="brand"><span class="brand__dot"></span><span>Meridian Care Partners</span></div>
</section>

</body>
</html>
```